Tessel Mobile website

Hello. Pray all is well. Peace be with you.

looking to make a website with pages information from https://veradilo.us. English and Spanish.

the header of quarnetel.com when in mobile version

clean vector images and layout of fendlecell.com

and the clean simple black and white look of tavesport.com

please use the attached logo for color guidance

also need the my account section for users to be designed

there should also be a countdown timer for days:hours:seconds on the home page

please do website in figma

```html
<!DOCTYPE html>
<html lang="en">
<head>
<meta charset="utf-8">
<title>Tessel Mobile</title>
<link href="https://fonts.googleapis.com/css2?family=Roboto:ital,wght@0,400;0,500;0,700;1,400&display=swap" rel="stylesheet">
<style>
:root{
  --ink:#000;
  --white:#fff;
  --soft:#e9e9e9;
  --panel:#f3f3f3;
  --muted:#555;
  --line:#cfcfcf;
  --star:#f5a623;
}
*{box-sizing:border-box;margin:0;padding:0}
html,body{width:1200px;height:3720px;overflow:hidden;background:var(--white)}
body{position:relative;font-family:'Roboto',sans-serif;color:var(--ink)}
.abs{position:absolute}
.countdown{left:0;top:0;width:1200px;height:39px;background:var(--ink);color:var(--white);display:flex;justify-content:center;align-items:center;gap:26px;font-size:15px}
.countdown b{font-size:18px;font-weight:700;margin-right:4px}
.brand{display:flex;align-items:center;gap:10px;font-weight:500}
.brand .mark{background:var(--ink)}
.header-brand{left:143px;top:52px;font-size:20px}
.header-brand .mark{width:34px;height:34px}
.nav{top:66px;left:0;font-size:14px;font-weight:500}
.nav a{position:absolute;color:var(--ink);text-decoration:none;white-space:nowrap}
.lang{left:930px;top:61px;width:72px;height:31px;border-radius:16px;background:var(--soft);display:flex;font-size:11px;font-weight:700}
.lang span{flex:1;display:flex;align-items:center;justify-content:center;border-radius:16px}
.lang .on{background:var(--ink);color:var(--white)}
.account{left:1024px;top:61px;width:32px;height:31px;border:2px solid var(--ink);display:flex;align-items:center;justify-content:center}
.hero-art{left:143px;top:137px;width:913px;height:441px;background:linear-gradient(135deg,#ececec,#d6d6d6 50%,#ececec)}
.hero-mascot{left:729px;top:137px;width:210px;height:488px;background:linear-gradient(180deg,#4a4a4a,#b9ab9a 55%,#6b6b6b)}
.hero-card{left:224px;top:228px;width:455px;height:260px;background:var(--white);padding:20px 30px}
.hero-card h1{font-size:50px;font-weight:500;line-height:1;margin-top:8px}
.hero-card p{font-size:17px;line-height:28px;margin-top:14px;white-space:nowrap}
.btn-outline{border:3px solid var(--ink);background:var(--white);font-size:14px;font-weight:700;display:flex;align-items:center;justify-content:center;gap:6px}
.hero-btn{left:257px;top:410px;width:214px;height:48px}
.slide-arrow{width:45px;height:45px;background:var(--ink);display:flex;align-items:center;justify-content:center}
.perk{width:200px;text-align:center;font-size:14px;line-height:20px;font-weight:500}
.perk .disc{width:88px;height:88px;border-radius:50%;background:var(--soft);margin:0 auto 14px;display:flex;align-items:center;justify-content:center}
.section-title{font-size:36px;font-weight:500;line-height:44px;text-transform:uppercase}
.offer{top:933px;width:575px;height:287px;background:var(--ink);color:var(--white);overflow:hidden}
.offer h3{position:absolute;font-size:25px;font-weight:500;line-height:32px}
.offer .visual{position:absolute}
.btn-solid{position:absolute;width:159px;height:48px;background:var(--white);color:var(--ink);font-size:14px;font-weight:700;display:flex;align-items:center;justify-content:center}
.step{width:226px;height:226px;border-radius:50%;background:var(--soft);text-align:center;font-size:16px;line-height:24px}
.step .disc{width:90px;height:90px;border-radius:50%;background:var(--white);margin:22px auto 16px;display:flex;align-items:center;justify-content:center}
.step-arrow{width:38px;height:38px;border-radius:50%;background:var(--ink);display:flex;align-items:center;justify-content:center}
.reviews{left:0;top:1690px;width:1200px;height:530px;background:linear-gradient(180deg,#000 0%,#555 30%,#f3f3f3 75%,#fff 100%)}
.review{background:var(--white);padding:20px 24px;box-shadow:0 6px 18px rgba(0,0,0,.12)}
.review .stars{color:var(--star);letter-spacing:2px}
.review q{display:block;font-style:italic;color:var(--muted);margin-top:12px;border-bottom:1px solid var(--line)}
.review .who{display:flex;align-items:center;gap:10px;margin-top:10px}
.review .face{border-radius:50%;background:linear-gradient(135deg,#c9a27e,#6d4c36)}
.review .who b{font-weight:500;display:block}
.quote-mark{font-size:90px;font-weight:700;line-height:1;font-family:'Roboto',serif}
.ring-ball{left:-32px;top:2259px;width:404px;height:404px;border-radius:50%;background:radial-gradient(circle at 65% 30%,#fff 0%,#555 22%,#000 60%)}
.faq-mascot{left:212px;top:2198px;width:228px;height:491px;background:linear-gradient(180deg,#4a4a4a,#b9ab9a 55%,#6b6b6b)}
.faq{left:526px;width:530px;height:53px;border:1px solid #aaa;display:flex;align-items:center;justify-content:space-between;padding:0 16px 0 15px;font-size:14px;color:#333}
.faq i{width:32px;height:32px;border-radius:50%;background:var(--ink);color:var(--white);font-style:normal;display:flex;align-items:center;justify-content:center;font-size:14px}
.blog-band{left:0;top:2784px;width:1200px;height:545px;background:var(--panel)}
.post{top:2920px;width:289px}
.post .photo{height:209px}
.post .date{position:absolute;left:13px;top:189px;width:144px;height:38px;background:var(--white);font-size:14px;font-weight:700;display:flex;align-items:center;justify-content:center;gap:5px}
.post h4{font-size:20px;font-weight:500;line-height:28px;margin-top:32px}
.post a{display:inline-block;margin-top:10px;font-size:14px;color:var(--ink)}
.footer-brand{left:143px;top:3398px;flex-direction:column;align-items:flex-start;gap:14px;font-size:52px;font-weight:400}
.footer-brand .mark{width:126px;height:126px;margin-left:102px}
.foot-col h5{font-size:24px;font-weight:500}
.foot-col .rule{width:80px;height:3px;margin:12px 0 18px;background:linear-gradient(90deg,var(--ink) 55%,#bbb 55%)}
.foot-col li{list-style:none;font-size:14px;line-height:32px;color:#222}
.divider{left:143px;top:3642px;width:913px;height:1px;background:#999}
.copy{left:0;top:3672px;width:1200px;text-align:center;font-size:14px;color:#333}
</style>
</head>
<body>

<div class="abs countdown"><span><b>20</b>Days</span><span><b>10</b>Hours</span><span><b>15</b>Mins</span><span><b>20</b>Secs</span></div>

<div class="abs brand header-brand"><span class="mark"></span>tesselmobile</div>
<nav class="abs nav">
  <a style="left:362px">Bring your own phone</a>
  <a style="left:540px">Coverage Check</a>
  <a style="left:680px">About us</a>
  <a style="left:774px">Support</a>
  <a style="left:862px">Blog</a>
</nav>
<div class="abs lang"><span class="on">En</span><span>Es</span></div>
<div class="abs account"><svg width="12" height="12" viewBox="0 0 12 12"><circle cx="6" cy="3.5" r="2.6"/><path d="M1 12c0-3 2.2-5 5-5s5 2 5 5z"/></svg></div>

<div class="abs hero-art" role="img" aria-label="Grey and white geometric line pattern backdrop"></div>
<div class="abs hero-mascot" role="img" aria-label="Cartoon wolf mascot giving a thumbs up"></div>
<div class="abs hero-card">
  <h1>TESSEL MOBILE</h1>
  <p>Lorem ipsum dolor sit amet, consectetur adipiscing<br>elit, sed do eiusmod tempor incididunt ut<br>labore et dolore magna aliqua.</p>
</div>
<div class="abs btn-outline hero-btn">VIEW ALL OFFERS <span>&#10230;</span></div>
<div class="abs slide-arrow" style="left:98px;top:329px"><svg width="10" height="10" viewBox="0 0 10 10"><path d="M6.5 2 3.5 5l3 3" stroke="#fff" stroke-width="1.6" fill="none"/></svg></div>
<div class="abs slide-arrow" style="left:1057px;top:329px"><svg width="10" height="10" viewBox="0 0 10 10"><path d="M3.5 2l3 3-3 3" stroke="#fff" stroke-width="1.6" fill="none"/></svg></div>

<div class="abs perk" style="left:158px;top:643px"><div class="disc"><svg width="44" height="34" viewBox="0 0 44 34" fill="none" stroke="#000" stroke-width="1.6"><rect x="2" y="4" width="26" height="20"/><path d="M28 11h8l6 7v6H28"/><circle cx="10" cy="27" r="4"/><circle cx="34" cy="27" r="4"/></svg></div>Free 2-day shipping,<br>seriously!</div>
<div class="abs perk" style="left:387px;top:643px"><div class="disc"><svg width="44" height="36" viewBox="0 0 44 36" fill="none" stroke="#000" stroke-width="1.6"><rect x="2" y="3" width="36" height="24" rx="2"/><path d="M2 10h36M7 17h12M7 21h8"/><circle cx="34" cy="27" r="7"/><path d="M29 32l10-10"/></svg></div>No credit check, no<br>stress</div>
<div class="abs perk" style="left:615px;top:643px"><div class="disc"><svg width="40" height="40" viewBox="0 0 40 40" fill="none" stroke="#000" stroke-width="1.6"><path d="M14 26c4-12 12-20 22-22-2 10-10 18-22 22z"/><path d="M14 26l-6-2 6-8M14 26l2 6 8-6M8 32l-4 4M12 34l-2 4"/><circle cx="26" cy="14" r="3"/></svg></div>5G speed at full<br>throttle!</div>
<div class="abs perk" style="left:843px;top:643px"><div class="disc"><svg width="40" height="40" viewBox="0 0 40 40" fill="none" stroke="#000" stroke-width="1.6"><path d="M6 20h6v16H6zM12 22l6-10 2 2-2 6h12a2 2 0 0 1 0 4l-2 10H12"/><path d="M20 3l1.5 3 3 .4-2.2 2 .6 3-2.9-1.6-2.9 1.6.6-3-2.2-2 3-.4zM30 6l1 2 2 .3-1.5 1.4.4 2-1.9-1-1.9 1 .4-2L27 8.3l2-.3z"/></svg></div>Zero annual contracts,<br>zero hassle!</div>

<h2 class="abs section-title" style="left:143px;top:828px">Incredible offers and<br>benefits you can't miss</h2>
<div class="abs btn-outline" style="left:842px;top:830px;width:214px;height:48px">VIEW ALL OFFERS <span>&#10230;</span></div>

<div class="abs offer" style="left:13px">
  <div class="visual" role="img" aria-label="Smartphone with a pink and violet screen" style="left:56px;top:36px;width:179px;height:251px;background:linear-gradient(180deg,#e0457e,#7a4fd0)"></div>
  <h3 style="left:271px;top:36px">BRING YOUR OWN<br>PHONE AND USE IT<br>WITH TESSEL<br>MOBILE!</h3>
  <div class="btn-solid" style="left:377px;top:199px">EXPLORE NOW</div>
</div>
<div class="abs offer" style="left:609px">
  <div class="visual" role="img" aria-label="Smartphone with a bright blue screen" style="left:26px;top:26px;width:230px;height:261px;background:linear-gradient(180deg,#1e6bff,#0aa7e8)"></div>
  <h3 style="left:262px;top:30px">BRING YOUR OWN<br>PHONE AND USE IT<br>WITH TESSEL<br>MOBILE!</h3>
  <div class="btn-solid" style="left:377px;top:199px">EXPLORE NOW</div>
</div>

<h2 class="abs section-title" style="left:0;top:1300px;width:1200px;text-align:center;font-size:34px">Easy activation process</h2>
<div class="abs step" style="left:144px;top:1376px"><div class="disc"><svg width="40" height="44" viewBox="0 0 40 44" fill="none" stroke="#000" stroke-width="1.6"><rect x="6" y="2" width="22" height="38" rx="3"/><path d="M12 26v-4M16 26v-8M20 26v-11"/><circle cx="29" cy="33" r="7"/><path d="M26 33l2 2 4-4"/></svg></div>Check Coverage<br>in your area</div>
<div class="abs step" style="left:372px;top:1376px"><div class="disc"><svg width="40" height="44" viewBox="0 0 40 44" fill="none" stroke="#000" stroke-width="1.6"><rect x="10" y="2" width="18" height="28" rx="3"/><path d="M16 40l-6-10c-1-3 2-4 4-2l2 3V16c0-2 3-2 3 0v8l8 2c3 1 4 3 3 6l-2 8"/></svg></div>Bring your phone or<br>get a new one</div>
<div class="abs step" style="left:602px;top:1376px"><div class="disc"><svg width="40" height="44" viewBox="0 0 40 44" fill="none" stroke="#000" stroke-width="1.6"><circle cx="20" cy="16" r="12"/><circle cx="20" cy="16" r="8"/><path d="M20 11l1.5 3 3 .4-2.2 2 .6 3-2.9-1.6-2.9 1.6.6-3-2.2-2 3-.4zM12 26l-5 12 6-2 3 5 4-13M28 26l5 12-6-2-3 5-4-13"/></svg></div>Choose the plan<br>you like best</div>
<div class="abs step" style="left:830px;top:1376px"><div class="disc"><svg width="40" height="44" viewBox="0 0 40 44" fill="none" stroke="#000" stroke-width="1.6"><rect x="6" y="4" width="24" height="34" rx="2"/><path d="M11 13h14M11 20h12M11 27h8M34 14l-12 18-3 2 1-4 12-18z"/></svg></div>Place your order and<br>activate your plan</div>
<div class="abs step-arrow" style="left:304px;top:1377px"><svg width="18" height="18" viewBox="0 0 18 18" fill="none" stroke="#fff" stroke-width="1.8"><path d="M3 9a6 6 0 0 1 12 0M12 7l3 3 3-3"/></svg></div>
<div class="abs step-arrow" style="left:561px;top:1522px"><svg width="18" height="18" viewBox="0 0 18 18" fill="none" stroke="#fff" stroke-width="1.8"><path d="M3 9a6 6 0 0 0 12 0M12 11l3-3 3 3"/></svg></div>
<div class="abs step-arrow" style="left:771px;top:1377px"><svg width="18" height="18" viewBox="0 0 18 18" fill="none" stroke="#fff" stroke-width="1.8"><path d="M3 9a6 6 0 0 1 12 0M12 7l3 3 3-3"/></svg></div>
<div class="abs step-arrow" style="left:1029px;top:1522px"><svg width="18" height="18" viewBox="0 0 18 18" fill="none" stroke="#fff" stroke-width="1.8"><path d="M3 9a6 6 0 0 0 12 0M12 11l3-3 3 3"/></svg></div>

<div class="abs reviews"></div>
<h2 class="abs section-title" style="left:0;top:1764px;width:1200px;text-align:center;color:#fff;font-size:34px">Tessel Mobile's the best</h2>
<div class="abs review" style="left:143px;top:1850px;width:273px;height:224px;font-size:13px;line-height:22px"><div class="stars">★★★★★</div><q>Lorem ipsum dolor sit amet, conse ctetur adipiscing elit, sed do eiusmod tempor incididunt ut labore et dolore magna aliqua.</q><div class="who"><span class="face" role="img" aria-label="Customer portrait" style="width:58px;height:58px"></span><span><b>John Doe</b>Company name</span></div></div>
<div class="abs review" style="left:770px;top:1850px;width:286px;height:224px;font-size:13px;line-height:22px"><div class="stars">★★★★★</div><q>Lorem ipsum dolor sit amet, conse ctetur adipiscing elit, sed do eiusmod tempor incididunt ut labore et dolore magna aliqua.</q><div class="who"><span class="face" role="img" aria-label="Customer portrait" style="width:58px;height:58px"></span><span><b>John Doe</b>Company name</span></div></div>
<div class="abs review" style="left:430px;top:1830px;width:340px;height:260px;font-size:16px;line-height:26px;padding:16px 26px"><div class="stars">★★★★★</div><q>Lorem ipsum dolor sit amet, conse ctetur adipiscing elit, sed do eiusmod tempor incididunt ut labore et dolore magna aliqua.</q><div class="who"><span class="face" role="img" aria-label="Customer portrait" style="width:70px;height:70px"></span><span style="font-size:15px;line-height:20px"><b>John Doe</b>Company name</span></div></div>
<div class="abs quote-mark" style="left:368px;top:2046px;font-size:80px">&ldquo;</div>
<div class="abs quote-mark" style="left:690px;top:2062px">&ldquo;</div>
<div class="abs quote-mark" style="left:989px;top:2046px;font-size:80px">&ldquo;</div>
<svg class="abs" style="left:62px;top:1945px" width="20" height="26" viewBox="0 0 20 26"><path d="M14 3 5 13l9 10" stroke="#fff" stroke-width="2.5" fill="none"/></svg>
<svg class="abs" style="left:1118px;top:1945px" width="20" height="26" viewBox="0 0 20 26"><path d="M6 3l9 10-9 10" stroke="#fff" stroke-width="2.5" fill="none"/></svg>

<div class="abs ring-ball" role="img" aria-label="Large dark glossy sphere"></div>
<div class="abs faq-mascot" role="img" aria-label="Cartoon wolf mascot leaning with a thumbs up"></div>
<h2 class="abs section-title" style="left:526px;top:2224px">The answer to all<br>your questions</h2>
<div class="abs faq" style="top:2331px">Lorem ipsum dolor sit amet, consectetur adipiscing elit<i>+</i></div>
<div class="abs faq" style="top:2403px">Lorem ipsum dolor sit amet, consectetur adipiscing elit<i>+</i></div>
<div class="abs faq" style="top:2475px">Lorem ipsum dolor sit amet, consectetur adipiscing elit<i>+</i></div>
<div class="abs faq" style="top:2547px">Lorem ipsum dolor sit amet, consectetur adipiscing elit<i>+</i></div>
<div class="abs faq" style="top:2619px">Lorem ipsum dolor sit amet, consectetur adipiscing elit<i>+</i></div>

<div class="abs blog-band"></div>
<h2 class="abs section-title" style="left:0;top:2859px;width:1226px;text-align:center">Latest blog</h2>
<div class="abs post" style="left:143px"><div class="photo" role="img" aria-label="Woman on a sofa smiling at her phone" style="background:linear-gradient(135deg,#6f7a55,#d9b98f 55%,#e9e2d6)"></div><span class="date">&#128197; MAR 21,2025</span><h4>Lorem ipsum dolor sit amet, consectetur adipiscing</h4><a>Read More &#10230;</a></div>
<div class="abs post" style="left:455px"><div class="photo" role="img" aria-label="Hands holding a phone in a cafe" style="background:linear-gradient(135deg,#3d5570,#a48a66 55%,#d9cbb5)"></div><span class="date">&#128197; MAR 21,2025</span><h4>Lorem ipsum dolor sit amet, consectetur adipiscing</h4><a>Read More &#10230;</a></div>
<div class="abs post" style="left:767px"><div class="photo" role="img" aria-label="Man in the city smiling at his phone" style="background:linear-gradient(135deg,#8a8f95,#2f4a7a 50%,#4f7a3c)"></div><span class="date">&#128197; MAR 21,2025</span><h4>Lorem ipsum dolor sit amet, consectetur adipiscing</h4><a>Read More &#10230;</a></div>
<svg class="abs" style="left:62px;top:3088px" width="20" height="26" viewBox="0 0 20 26"><path d="M14 3 5 13l9 10" stroke="#000" stroke-width="2.5" fill="none"/></svg>
<svg class="abs" style="left:1118px;top:3088px" width="20" height="26" viewBox="0 0 20 26"><path d="M6 3l9 10-9 10" stroke="#000" stroke-width="2.5" fill="none"/></svg>

<div class="abs brand footer-brand"><span class="mark"></span>tesselmobile</div>
<div class="abs foot-col" style="left:543px;top:3386px"><h5>QUICK LINKS</h5><div class="rule"></div><ul><li>Home</li><li>My account</li><li>Planes</li><li>Telephones</li><li>Add data</li></ul></div>
<div class="abs foot-col" style="left:735px;top:3386px"><h5>ABOUT US</h5><div class="rule"></div><ul><li>Why Tessel Mobile?</li><li>Contact</li><li>Coverage information</li><li>Reviews</li><li>Blog</li></ul></div>
<div class="abs foot-col" style="left:930px;top:3386px"><h5>FEATURE</h5><div class="rule"></div><ul><li>Bring your phone</li><li>Check your device</li><li>Check your coverage</li></ul></div>
<div class="abs divider"></div>
<div class="abs copy">© Copyrights 2025 | All Rights Reserved</div>

</body>
</html>
```